Catering Menu Package

I currently have a complete menu package, which we have redesigned as far as content, now I need to it put together in a catalog type format. It is essentially 10-12 pages in length, and will be sent for print production. Upon receiving a final edit
Updates

I have added an example gif to the project.

I did this free hand this basically what I am looking for. please change text and type to whatever you think would look best. This is a total rough design so, feel free to change any and everything. The text for the page is on the word documents. If you need more images let me know I am in the process of getting as many images uploaded for your use.

Project Deadline Extended
Reason: I figured we got a late jump with questions, so i am extending a few days .

Target Market(s)

The target market is business who wish to have catered luncheons, breakfasts , meetings

Industry/Entity Type

Catering

Requirements
Must have
• I have attached a copy of the text that what we want in the package, our logo, and i have also attached a catering package of another company to give you an idea what the finished product will be
Should not have
• It should not look identical to the example catering packages, these are for some inspiration we want our own design with the same type of look and feel

```html
<!DOCTYPE html>
<html lang="en">
<head>
<meta charset="utf-8">
<title>Entrée Salads — Meadowbrook Hill Caterers</title>
<link rel="stylesheet" href="https://fonts.googleapis.com/css2?family=Alegreya:ital,wght@0,400;0,500;1,600&family=Pinyon+Script&display=swap">
<style>
  :root {
    --paper: #ffffff;
    --mist: #e9e7e6;
    --strip-top: #f6f2ee;
    --strip-bottom: #e6d9cf;
    --ink: #5a4a42;
    --title: #6d6b69;
    --green: #8aa654;
    --brand: #1d1d1d;
    --photo-light: #e8e6df;
    --photo-mid: #b9b27a;
    --photo-dark: #5f6a3c;
  }
  * { box-sizing: border-box; margin: 0; padding: 0; }
  html, body { width: 1200px; height: 927px; overflow: hidden; }
  body { background: var(--paper); font-family: "Alegreya", Georgia, serif; color: var(--ink); }

  .menu-page {
    position: relative;
    width: 1200px;
    height: 927px;
    background: radial-gradient(ellipse 900px 300px at 620px 0, var(--mist) 0%, var(--paper) 100%);
    overflow: hidden;
  }
  .side-strip {
    position: absolute; left: 0; top: 0;
    width: 184px; height: 927px;
    background: linear-gradient(180deg, var(--strip-top) 0%, var(--paper) 35%, var(--strip-bottom) 100%);
  }

  .brand {
    position: absolute; left: 28px; top: 30px; width: 132px;
    text-align: center;
  }
  .brand-mark {
    display: block; width: 120px; height: 120px; margin: 0 auto 14px;
    border: 3px solid var(--brand); border-radius: 50%;
  }
  .brand-name {
    font-family: "Alegreya", Georgia, serif;
    font-weight: 500; font-size: 19px; line-height: 25px;
    color: var(--brand); text-transform: lowercase;
  }

  .page-title {
    position: absolute; left: 196px; top: 38px;
    font-family: "Pinyon Script", cursive;
    font-weight: 400; font-size: 50px; color: var(--title);
  }

  .salad {
    position: absolute; width: 465px;
  }
  .salad-name {
    font-style: italic; font-weight: 600;
    font-size: 19px; line-height: 24px; color: var(--green);
  }
  .salad-desc {
    font-size: 16.5px; line-height: 24.5px; color: var(--ink);
  }
  .price { margin-left: 14px; }

  .col-left { left: 197px; }
  .col-right { left: 692px; width: 470px; }

  .dish-photo {
    position: absolute; left: 674px; top: 583px;
    width: 526px; height: 344px;
    background:
      radial-gradient(ellipse 230px 120px at 310px 190px, var(--photo-mid) 0%, var(--photo-dark) 55%, transparent 80%),
      linear-gradient(160deg, var(--photo-light) 0%, #d9d6cc 100%);
    -webkit-mask-image: radial-gradient(ellipse 120% 120% at 100% 100%, #000 70%, transparent 100%);
    mask-image: radial-gradient(ellipse 120% 120% at 100% 100%, #000 70%, transparent 100%);
  }
</style>
</head>
<body>
<main class="menu-page">
  <div class="side-strip"></div>

  <div class="brand">
    <span class="brand-mark"></span>
    <div class="brand-name">meadowbrook<br>hill<br>caterers</div>
  </div>

  <h1 class="page-title">Entrée Salads</h1>

  <section class="salad col-left" style="top:126px">
    <h2 class="salad-name">California Cobb</h2>
    <p class="salad-desc">Spring Mix topped with House Roasted Turkey Breast, Applewood Smoked Bacon Bits, Diced Tomatoes, Avocado Slices, Roasted Red Peppers, &amp; Kalamata Olives.<span class="price">$&amp;.&amp;&amp;</span></p>
  </section>

  <section class="salad col-left" style="top:270px">
    <h2 class="salad-name">Titanic</h2>
    <p class="salad-desc">Iceberg wedge topped with Diced Tomatoes, Applewood Smoked Bacon Bits &amp; our House-made Bleu Cheese Dressing.<span class="price">$&amp;.&amp;&amp;</span></p>
  </section>

  <section class="salad col-left" style="top:392px">
    <h2 class="salad-name">MHC Chef Salad</h2>
    <p class="salad-desc">House Roasted Turkey Breast, Black Forest Ham. American &amp; Swiss Cheeses, diced Tomatoes served over Crisp Romaine Lettuce.<span class="price">$&amp;.&amp;&amp;</span></p>
  </section>

  <section class="salad col-left" style="top:513px">
    <h2 class="salad-name">Grilled Chicken &amp; Organic Spinach</h2>
    <p class="salad-desc">Grilled Chicken Breast strips served over Organic Baby Spinach topped with Crumbled Gorgonzola Cheese, Julienne Red Onions, Button Mushroom Slices, &amp; Garlic Croutons.<span class="price">$&amp;.&amp;&amp;</span></p>
  </section>

  <section class="salad col-left" style="top:658px">
    <h2 class="salad-name">Bistro Steak Salad</h2>
    <p class="salad-desc">Grilled Bistro Tenderloin served over Spring Mix topped with Sliced Button Mushrooms, Red Onions, Shredded Carrots, Grape Tomatoes, Crumbled Gorgonzola Cheese, &amp; Walnut Halves.<span class="price">$&amp;.&amp;&amp;</span></p>
  </section>

  <section class="salad col-right" style="top:173px">
    <h2 class="salad-name">Grilled Vegetable Salad</h2>
    <p class="salad-desc">BalsamicMarinated Grilled Vegetables served over Spring Mix with Avocado slices, Feta Cheese, &amp; Pepperoncinis.<span class="price">$&amp;.&amp;&amp;</span></p>
  </section>

  <section class="salad col-right" style="top:295px">
    <h2 class="salad-name">Micro Power Green Salad</h2>
    <p class="salad-desc">Blend of Micro Spinach, Kale, Chard &amp; Arugala, topped with Goat Cheese, Oven Roasted Beets, Almond Slivers, Julienne Carrots &amp; finished with a House-made Shitake-Sesame Vinaigrette.<span class="price">$&amp;.&amp;&amp;</span></p>
  </section>

  <section class="salad col-right" style="top:438px">
    <h2 class="salad-name">Powerhouse Salad</h2>
    <p class="salad-desc">Spring Mix Lettuces topped with a generous scoop of Tuna Salad, Egg Whites, Shredded Carrots, Cucumbers, Grape Tomatoes, &amp; Broccoli Florets.<span class="price">$&amp;.&amp;&amp;</span></p>
  </section>

  <div class="dish-photo" role="img" aria-label="Photo of a plate of grilled vegetables: zucchini, eggplant, red and yellow peppers and onion with rosemary"></div>
</main>
</body>
</html>
```